Business Card Design

WE are looking for a premium quality Business Cards for a Law Firm . Copies of our current business card is attached.

Contact Information for Business Card

xyz

```html
<!DOCTYPE html>
<html lang="en">
<head>
<meta charset="utf-8">
<title>Harlow Lawyers – Business Card</title>
<link href="https://fonts.googleapis.com/css2?family=Cinzel:wght@500;600;700&family=Arimo:wght@400;700&display=swap" rel="stylesheet">
<style>
  :root {
    --bg: #d9d9db;
    --card-white: #ffffff;
    --gold: #c49a55;
    --green: #0f2a1f;
    --ink: #1c1c1c;
    --rule: #2a2a2a;
    --white: #ffffff;
  }
  * { margin: 0; padding: 0; box-sizing: border-box; }
  html, body { width: 1200px; height: 800px; overflow: hidden; }
  body {
    background: var(--bg);
    font-family: "Arimo", Arial, sans-serif;
    position: relative;
  }
  .card {
    position: absolute;
    width: 520px;
    height: 297px;
    border-radius: 22px;
    overflow: hidden;
    top: 252px;
  }
  .card-front { left: 45px; background: var(--card-white); }
  .card-back { left: 635px; background: var(--gold); border-bottom: 3px solid var(--green); }

  .front-band { position: absolute; left: 0; top: 0; width: 520px; height: 297px; }

  .brand {
    position: absolute;
    display: flex;
    align-items: center;
    gap: 10px;
    font-family: "Cinzel", Georgia, serif;
    font-weight: 600;
  }
  .brand-mark { border-radius: 50%; flex: none; }
  .brand-name { line-height: 1.05; text-align: center; }
  .brand-name span { display: block; }

  .front-brand { right: 36px; top: 22px; color: var(--green); }
  .front-brand .brand-mark { width: 30px; height: 30px; border: 2px solid var(--gold); }
  .front-brand .brand-name { font-size: 26px; }
  .front-brand .brand-name .sub { font-size: 11px; letter-spacing: 7px; color: var(--gold); }

  .office-address {
    position: absolute;
    right: 32px;
    top: 96px;
    width: 210px;
    border-top: 1px solid var(--rule);
    padding-top: 7px;
    text-align: right;
    font-size: 13px;
    line-height: 1.32;
    font-style: normal;
    color: var(--ink);
  }

  .person {
    position: absolute;
    left: 34px;
    top: 112px;
    width: 230px;
  }
  .person-name {
    font-family: "Cinzel", Georgia, serif;
    font-weight: 700;
    font-size: 19px;
    line-height: 1.25;
    color: var(--green);
    letter-spacing: 0.5px;
  }
  .person-role, .person-cred {
    font-size: 12px;
    color: var(--gold);
    line-height: 1.3;
  }
  .contact-list {
    list-style: none;
    margin-top: 6px;
    padding-top: 6px;
    border-top: 1px solid var(--rule);
    font-size: 12.5px;
    color: var(--ink);
    line-height: 1.3;
  }
  .contact-list li { display: flex; align-items: center; gap: 6px; }
  .contact-list svg { width: 10px; height: 11px; flex: none; }
  .contact-list .no-icon { padding-left: 16px; }

  .website {
    position: absolute;
    left: 34px;
    top: 257px;
    color: var(--white);
    font-size: 14px;
    letter-spacing: 1px;
  }

  .back-brand { left: 0; right: 0; top: 40px; justify-content: center; color: var(--white); }
  .back-brand .brand-mark { width: 40px; height: 40px; border: 2.5px solid var(--white); }
  .back-brand .brand-name { font-size: 36px; }
  .back-brand .brand-name .sub { font-size: 14px; letter-spacing: 10px; }

  .offices {
    position: absolute;
    left: 20px;
    right: 20px;
    bottom: 34px;
    display: flex;
    color: var(--white);
    text-align: center;
  }
  .office {
    flex: 1;
    font-size: 11px;
    line-height: 1.35;
    padding: 4px 6px;
  }
  .office + .office { border-left: 1px solid rgba(255,255,255,0.75); }
  .office h3 { font-size: 13px; font-weight: 700; margin-bottom: 2px; }
  .office .phone b { font-weight: 700; }
</style>
</head>
<body>

<section class="card card-front" aria-label="Business card front">
  <svg class="front-band" viewBox="0 0 520 297" aria-hidden="true">
    <path d="M0 245 H328 L348 268 H520 V297 H0 Z" fill="#0f2a1f"/>
    <rect x="0" y="289" width="520" height="8" fill="#c49a55"/>
  </svg>

  <div class="brand front-brand">
    <div class="brand-mark"></div>
    <div class="brand-name"><span>HARLOW</span><span class="sub">LAWYERS</span></div>
  </div>

  <address class="office-address">
    Level 3, Harlow House<br>
    48 Ashford Terrace<br>
    Kelvin Hill, QLD 4000
  </address>

  <div class="person">
    <div class="person-name">DANIEL MERCER</div>
    <div class="person-role">Director &amp; Principal Solicitor</div>
    <div class="person-cred">MBA, Juris Doctor</div>
    <ul class="contact-list">
      <li>
        <svg viewBox="0 0 10 11" aria-label="Phone"><path d="M2 0.5 L4 2.5 L3 4 Q4.5 6.5 6.5 7.5 L7.8 6.5 L9.8 8.5 L8.5 10.3 Q4 10 1 5 Q0.5 2 2 0.5Z" fill="#1c1c1c"/></svg>
        +61 7 3000 1482
      </li>
      <li>
        <svg viewBox="0 0 10 11" aria-label="Mobile"><rect x="1.5" y="0.5" width="7" height="10" rx="1" fill="none" stroke="#1c1c1c" stroke-width="1.2"/></svg>
        +61 0400 612 397
      </li>
      <li class="no-icon">daniel@harlowlawyers.com.au</li>
    </ul>
  </div>

  <div class="website">www.harlowlawyers.com.au</div>
</section>

<section class="card card-back" aria-label="Business card back">
  <div class="brand back-brand">
    <div class="brand-mark"></div>
    <div class="brand-name"><span>HARLOW</span><span class="sub">LAWYERS</span></div>
  </div>

  <div class="offices">
    <div class="office">
      <h3>Melbourne</h3>
      Level 12, 88 Bramley Street<br>
      Melbourne, VIC 3000<br>
      <span class="phone"><b>Phone :</b> +61 03 9000 2471</span>
    </div>
    <div class="office">
      <h3>Sydney</h3>
      Level 9, Corbett Building<br>
      21 Marlow Street<br>
      Parramatta, NSW 2150<br>
      <span class="phone"><b>Phone :</b> +61 02 8000 3569</span>
    </div>
    <div class="office">
      <h3>Perth</h3>
      Level 18, Rowan Tower<br>
      72 Elmsford Terrace<br>
      Perth, WA 6000<br>
      <span class="phone"><b>Phone :</b> +61 08 6000 2813</span>
    </div>
  </div>
</section>

</body>
</html>
```